Wealth Education Business Needs Sharp Business Card Design

We need a business card design for a recently launched investor education business called Harbor Crest.

The final design should promote security, empowerment, self improvement and financial gain. The card will ideally promote the stature of the business.

For more information and colours please visit harborcrest.com.au

Target Market(s)

Corporate executives and high net worth individuals

Industry/Entity Type

Education

Contact Information for Business Card

```html
<!DOCTYPE html>
<html lang="en">
<head>
<meta charset="UTF-8">
<title>Harbor Crest — Business Card</title>
<link href="https://fonts.googleapis.com/css2?family=Lato:wght@400;700&display=swap" rel="stylesheet">
<style>
  :root {
    --stage: #e9e7e4;
    --navy: #1f2d40;
    --paper: #fdfdfc;
    --ink: #2b2b2b;
    --ink-soft: #4a4a4a;
    --teal: #1a9aa0;
    --teal-light: #3fc1c6;
    --band-grey: #58585b;
    --white: #ffffff;
  }
  * { margin: 0; padding: 0; box-sizing: border-box; }
  html, body {
    width: 1200px; height: 960px; overflow: hidden;
    background: var(--stage);
    font-family: "Lato", Arial, sans-serif;
  }
  .canvas { position: relative; width: 1200px; height: 960px; }

  .card {
    position: absolute; left: 270px; width: 645px; height: 369px;
    overflow: hidden;
  }
  .card--front { top: 83px; background: var(--navy); }
  .card--back { top: 507px; background: var(--paper); }

  .wordmark {
    position: absolute; font-weight: 400; text-transform: uppercase;
    white-space: nowrap; line-height: 1;
  }
  .card--front .wordmark {
    left: 0; right: 0; top: 165px; text-align: center;
    font-size: 42px; letter-spacing: 6px; color: var(--white);
  }
  .card--back .wordmark {
    left: 52px; top: 72px; font-size: 29px; letter-spacing: 4px; color: var(--ink);
  }

  .front-url {
    position: absolute; left: 0; right: 0; top: 316px; text-align: center;
    font-size: 14px; color: var(--white);
  }
  .front-url .domain { color: var(--teal-light); }

  .person { position: absolute; left: 52px; top: 177px; }
  .person__name { font-size: 19px; font-weight: 700; color: var(--teal); line-height: 1.2; }
  .person__role { font-size: 14.5px; color: var(--ink-soft); margin-top: 2px; }

  .contact { position: absolute; left: 379px; top: 179px; font-size: 14.5px; color: var(--ink-soft); }
  .contact__address { line-height: 19px; }
  .contact__list { list-style: none; margin-top: 22px; }
  .contact__list li { display: flex; align-items: center; height: 20.5px; }
  .contact__list svg { width: 16px; height: 16px; margin-right: 13px; flex: none; }

  .band { position: absolute; bottom: 0; height: 12px; }
  .band--teal { left: 0; width: 295px; background: var(--teal); }
  .band--grey { left: 350px; right: 0; background: var(--band-grey); }
</style>
</head>
<body>
<div class="canvas">

  <section class="card card--front" aria-label="Card front">
    <div class="wordmark">Harbor Crest</div>
    <p class="front-url">www.<span class="domain">harborcrest.com</span>.au</p>
  </section>

  <section class="card card--back" aria-label="Card back">
    <div class="wordmark">Harbor Crest</div>

    <div class="person">
      <p class="person__name">Daniel Hartley</p>
      <p class="person__role">Founder &amp; CEO</p>
    </div>

    <div class="contact">
      <p class="contact__address">Level 2, 47 Collins Row<br>Melbourne VIC 3000</p>
      <ul class="contact__list">
        <li>
          <svg viewBox="0 0 16 16" aria-hidden="true"><path fill="#1a9aa0" d="M1 5c0-2 3-3 7-3s7 1 7 3v1.5h-3.5V5h-7v1.5H1z M4 7h8l2 7H2z"/><circle cx="8" cy="10.5" r="1.8" fill="#fdfdfc"/></svg>
          1300.555.482
        </li>
        <li>
          <svg viewBox="0 0 16 16" aria-hidden="true"><rect x="4" y="1" width="8" height="14" rx="1.5" fill="none" stroke="#1a9aa0" stroke-width="1.4"/><circle cx="8" cy="12.6" r="0.9" fill="#1a9aa0"/></svg>
          0000.000.000
        </li>
        <li>
          <svg viewBox="0 0 16 16" aria-hidden="true"><rect x="1" y="3" width="14" height="10" fill="#1a9aa0"/><path d="M1.5 3.5 8 9l6.5-5.5M1.5 12.5l5-4.5M14.5 12.5l-5-4.5" fill="none" stroke="#fdfdfc" stroke-width="1.1"/></svg>
          support@harborcrest.com.au
        </li>
        <li>
          <svg viewBox="0 0 16 16" aria-hidden="true"><g fill="none" stroke="#1a9aa0" stroke-width="1.2"><circle cx="8" cy="8" r="6.5"/><ellipse cx="8" cy="8" rx="2.8" ry="6.5"/><path d="M1.5 8h13M2.6 4.5h10.8M2.6 11.5h10.8"/></g></svg>
          www.harborcrest.com.au
        </li>
      </ul>
    </div>

    <div class="band band--teal"></div>
    <div class="band band--grey"></div>
  </section>

</div>
</body>
</html>
```